Hop Bright Meadow Business Website Branding

Looking for a wordpress template design with CSS and HTML encoding. Current website can be seen at hopbrightmeadow.example.

WE ARE CURRENTLY IN PROCESS GETTING A LOGO DESIGN... I HAVE INCLUDED THE TOP POTENTIAL DESIGNS FOR REFERENCE TO HELP UNDERSTAND WHAT STYLE WE ARE LOOKING FOR...
NOTE: THE “PEBBLE CREW” LOGO WAS A PREVIOUS COMPANY WE OWNED SO YOU CAN GE A FEEL FOR THE TYPE OF DESIGNS WE HAVE USED IN THE PAST.

My blog will focus on making a connection with wild Florida, it’s wildlife, plants and animals... with an eye toward Florida conservation, nature adventure trips, and education... Content, photos and other merchandise will also be offered for sale.
I’m looking for a site design that incorporates Florida nature and wildlife/plants, with a fun “Old Florida” retro-adventure feel.
When they see this site it should speak to the import of natural Florida and the critical nature of the ecosystem here... while being instantly recognizable and iconic... IE: when I think of florida I think of water, plants, warmth, sunsets etc...

https://join.chatroomhub.example/t/lumexstudio-kzt4821/shared_invite/zt-pqwrt83m-hRnLvXaKoPzsYcB1Uq7JdM

Target Market(s)

Nature, Education, Conservation, Photography

Industry/Entity Type

Photographer

Coding

Coded - Design and coding required

Requirements
Must have
• Need to have site wide template design which generally includes a landing page and a general page template for other pages... Must include html and css encoding...
Should not have
• Any animals included in the site should be Florida native... IE: no African animals etc... This will require some research to ensure that if animals are included that they are part of the Florida ecosystem.

```html
<!DOCTYPE html>
<html lang="en">
<head>
<meta charset="utf-8">
<title>Hop Bright Meadow</title>
<link rel="stylesheet" href="https://fonts.googleapis.com/css2?family=Playball&family=Roboto:ital,wght@0,400;0,500;0,700;0,900;1,400&display=swap">
<style>
:root{
  --parchment:#e4d9b0;
  --parchment-dark:#d6c696;
  --parchment-light:#ece4c2;
  --ribbon:#efe8bd;
  --brown:#6e1f04;
  --brown-text:#7a2c0c;
  --ink:#2a2118;
  --gold:#d9b55a;
  --white:#ffffff;
  --leaf:#3f6a2a;
  --leaf-dark:#2c4c1e;
}
*{box-sizing:border-box;margin:0;padding:0}
html,body{width:1200px;height:4910px;overflow:hidden}
body{position:relative;font-family:"Roboto",sans-serif;color:var(--ink);
  background:linear-gradient(90deg,#d9cb9e 0%,#e8dfbb 40%,#e6dcb5 60%,#d4c393 100%)}
.abs{position:absolute}
.script{font-family:"Playball",cursive;color:var(--brown-text);font-weight:400}
.section-title{position:absolute;left:0;width:1200px;text-align:center;font-size:34px}
.rule{position:absolute;height:2px;background:var(--brown)}
.btn{position:absolute;background:var(--brown);color:var(--white);font-weight:700;font-size:16px;
  display:flex;align-items:center;justify-content:center;text-decoration:none}
.phone{left:945px;top:12px;font-family:"Playball",cursive;color:var(--brown-text);font-size:18px;display:flex;align-items:center;gap:6px}
.nav-ribbon{position:absolute;left:0;width:1200px;height:200px}
.nav-link{position:absolute;font-family:"Playball",cursive;color:var(--brown-text);font-size:22px;transform:translateX(-50%);white-space:nowrap}
.logo-circle{position:absolute;width:164px;height:164px;border-radius:50%;background:var(--ribbon);
  border:2px dashed #c9b57a;display:flex;flex-direction:column;align-items:center;justify-content:center;
  font-family:"Playball",cursive;color:var(--brown-text);font-size:30px;line-height:1;text-align:center}
.hero-text{position:absolute;left:0;width:1200px;text-align:center;color:var(--white)}
.hero-kicker{top:326px;font-family:"Playball",cursive;font-size:34px}
.hero-title{top:368px;font-weight:900;font-size:82px;letter-spacing:1px}
.hero-lede{top:480px;font-size:16px;font-weight:500;line-height:25px}
.dots{position:absolute;top:739px;left:562px;display:flex;gap:6px}
.dots span{width:10px;height:10px;border-radius:50%;background:var(--white)}
.dots span.on{background:transparent;border:2px solid var(--white)}
.welcome-title{left:124px;top:948px;font-size:34px}
.body-copy{font-size:16px;line-height:26px;color:#1f1a14}
.tab-band{position:absolute;left:0;top:1372px;width:1200px;height:127px;background:var(--parchment-light);border-bottom:2px solid #7b6a4a}
.tab{position:absolute;top:1447px;font-size:16px;color:#6c5f46;transform:translateX(-50%)}
.tab.active{color:var(--brown-text)}
.card{position:absolute;left:110px;top:1522px;width:326px;height:357px;background:var(--white)}
.photo{position:absolute}
.blog-photo{position:absolute;width:488px;height:278px;background:linear-gradient(135deg,var(--leaf) 0%,#4e7a34 50%,var(--leaf-dark) 100%)}
.blog-text{position:absolute;text-align:center;font-weight:700;font-size:16px;line-height:26px;color:var(--brown-text)}
.gallery-thumb{position:absolute;top:4261px;height:177px}
.subscribe-input{position:absolute;left:156px;top:4758px;width:368px;height:48px;background:var(--white);border:1px solid #8a7a5a;font-size:12px;padding-left:12px;display:flex;align-items:center;color:#333}
.social{position:absolute;top:4770px;width:34px;height:34px;border-radius:50%;background:var(--white)}
.copyright{position:absolute;top:4850px;left:0;width:1200px;text-align:center;font-size:16px;color:var(--brown-text)}
</style>
</head>
<body>

<!-- Hero -->
<svg class="abs" style="left:0;top:0" width="1200" height="820" role="img" aria-label="Photo of a wooden boardwalk through dune grass and palm trees leading to a beach at sunset">
  <defs>
    <linearGradient id="heroSky" x1="0" y1="0" x2="0" y2="1">
      <stop offset="0" stop-color="#8a8e94"/>
      <stop offset="0.35" stop-color="#c49a6a"/>
      <stop offset="0.55" stop-color="#8a6a3c"/>
      <stop offset="1" stop-color="#4d3f28"/>
    </linearGradient>
  </defs>
  <path d="M0 110 H1200 V750 C1000 760 850 700 650 760 C480 810 300 830 160 740 C70 680 20 600 0 510 Z" fill="url(#heroSky)"/>
  <path d="M1200 750 C1000 760 850 700 650 760 C480 810 300 830 160 740 C70 680 20 600 0 510" fill="none" stroke="var(--brown)" stroke-width="10"/>
</svg>
<div class="hero-text hero-kicker">Exploring Florida's Natural Wonders</div>
<div class="hero-text hero-title">DISCOVER FLORIDA</div>
<div class="hero-text hero-lede">Lorem ipsum dolor sit amet, consectetur adipiscing elit, sed do eiusmod tempor<br>incididunt ut labore et dolore magna aliqua.</div>
<div class="dots"><span></span><span class="on"></span><span></span><span></span><span></span></div>

<!-- Header -->
<div class="abs phone">
  <svg width="14" height="14" viewBox="0 0 14 14"><rect width="14" height="14" rx="2" fill="var(--brown)"/><path d="M4 3 L6 3 L6.5 5.5 L5.5 6.3 C6 7.5 6.8 8.3 8 8.8 L8.8 7.8 L11 8.3 L11 10.3 C7 10.5 3.6 7 4 3 Z" fill="#fff"/></svg>
  + 555 010 2044
</div>
<svg class="nav-ribbon" style="top:40px" viewBox="0 0 1200 200" width="1200" height="200">
  <path d="M72 22 H1140 L1120 62 L1140 110 H72 L92 62 Z" fill="#c9b57a"/>
  <path d="M100 14 H1100 V116 H100 Z" fill="var(--ribbon)"/>
  <path d="M112 22 H1088 M112 108 H1088" stroke="#b9a46a" stroke-width="1.5" stroke-dasharray="3 4"/>
</svg>
<div class="nav-link" style="left:229px;top:82px">Home</div>
<div class="nav-link" style="left:328px;top:82px">About Us</div>
<div class="nav-link" style="left:421px;top:82px">Blog</div>
<div class="nav-link" style="left:793px;top:82px">Gallery</div>
<div class="nav-link" style="left:890px;top:82px">Reviews</div>
<div class="nav-link" style="left:989px;top:82px">Contact</div>
<svg class="abs" style="left:1058px;top:89px" width="18" height="18" viewBox="0 0 18 18"><circle cx="7.5" cy="7.5" r="5.5" fill="none" stroke="var(--brown)" stroke-width="2.4"/><path d="M11.5 11.5 L16 16" stroke="var(--brown)" stroke-width="2.8"/></svg>
<div class="logo-circle" style="left:518px;top:24px">Hop Bright<br>Meadow</div>

<!-- Welcome -->
<h1 class="abs script welcome-title">Welcome To Hop Bright Meadow</h1>
<div class="rule" style="left:124px;top:1005px;width:115px"></div>
<p class="abs body-copy" style="left:124px;top:1031px;width:432px;font-size:16.5px">Come explore wild places and stunning scenery with me as I discover new and exciting eco-adventures and learn about the rare and unique wildlife and environments that make Florida so precious and extraordinary. I hope you can vicariously enjoy the wild and untamed beauty of Florida through my eyes, and learn some amazing things about nature on our explorations.</p>
<svg class="abs" style="left:638px;top:870px" width="450" height="410" role="img" aria-label="Photo of a green heron perched on a branch, framed in a rounded shape">
  <defs><linearGradient id="heronBg" x1="0" y1="0" x2="1" y2="1"><stop offset="0" stop-color="#4e8a2c"/><stop offset="1" stop-color="#2a5a1a"/></linearGradient></defs>
  <path d="M60 130 C90 50 240 40 320 90 C410 150 420 300 330 370 C250 420 90 410 40 320 C10 260 30 190 60 130 Z" fill="var(--gold)"/>
  <path d="M65 130 C95 60 240 50 315 98 C400 155 405 295 322 360 C245 408 95 398 48 314 C20 258 38 190 65 130 Z" fill="url(#heronBg)"/>
</svg>

<!-- Available in Florida -->
<div class="tab-band"></div>
<div class="abs script" style="left:124px;top:1428px;font-size:26px;line-height:26px;color:var(--ink);text-align:center">Available In<br>Florida</div>
<div class="tab active" style="left:349px">Animals</div>
<div class="tab" style="left:514px">Plants</div>
<div class="tab" style="left:678px">Scenaries</div>
<div class="tab" style="left:844px">Culture</div>
<div class="tab" style="left:1010px">Birds</div>

<div class="card">
  <div class="photo" role="img" aria-label="Photo of a Florida panther walking through woodland" style="left:0;top:0;width:326px;height:175px;background:linear-gradient(160deg,#6b6a52,#8b7a5a 50%,#3e3a2a)"></div>
  <div class="abs script" style="left:0;top:182px;width:326px;text-align:center;font-size:26px;color:var(--ink)">Animals</div>
  <p class="abs" style="left:30px;top:236px;width:266px;text-align:center;font-size:14px;line-height:26px;color:#555">Lorem ipsum dolor sit amet, consec tetur adipiscing elit, sed do eiusmod tempor incididunt ut.</p>
  <div class="btn" style="left:96px;top:331px;width:137px;height:48px;font-size:14px">Read More</div>
</div>
<div class="abs" role="img" aria-label="Dotted world map with Florida highlighted in blue" style="left:438px;top:1518px;width:728px;height:387px;background:linear-gradient(180deg,rgba(222,165,55,0.35),rgba(222,165,55,0.2))"></div>

<!-- Testimonials -->
<h2 class="script section-title" style="top:2062px">Client Testimonials</h2>
<div class="rule" style="left:542px;top:2117px;width:116px"></div>
<div class="abs script" style="left:0;width:1200px;top:2150px;text-align:center;font-size:60px;line-height:50px">&ldquo;</div>
<p class="abs" style="left:0;width:1200px;top:2192px;text-align:center;font-style:italic;font-size:16px;line-height:26px;color:#1f1a14">Nature has been for me, as long as I remember, a source of solace, inspiration, adventure,<br>and delight; a home, a teacher, a companion.</p>
<div class="abs script" style="left:0;width:1200px;top:2254px;text-align:center;font-size:16px;color:var(--brown-text)">Delia Farrow</div>

<!-- Blogs -->
<h2 class="script section-title" style="top:2452px">Our Latest Blogs</h2>
<div class="rule" style="left:542px;top:2513px;width:116px"></div>

<div class="blog-text" style="left:124px;top:2630px;width:446px">There is a way that nature speaks, that land speaks. Most of the time we are simply not patient enough, quiet enough, to pay attention to the story.</div>
<div class="btn" style="left:280px;top:2737px;width:135px;height:48px">Read More</div>
<div class="blog-photo" role="img" aria-label="Photo of a yellow wildflower among green leaves" style="left:600px;top:2572px"></div>

<div class="blog-photo" role="img" aria-label="Photo of a pale purple wildflower in tall grass" style="left:110px;top:2863px;width:490px"></div>
<div class="blog-text" style="left:668px;top:2940px;width:370px">Instructions for living a life. Pay attention. Be astonished. Tell about it.</div>
<div class="btn" style="left:785px;top:3031px;width:135px;height:46px">Read More</div>

<div class="blog-text" style="left:124px;top:3241px;width:446px">Those who contemplate the beauty of the earth find reserves of strength that will endure as long as life lasts.</div>
<div class="btn" style="left:280px;top:3324px;width:135px;height:48px">Read More</div>
<div class="blog-photo" role="img" aria-label="Photo of a pink pea flower among green leaves" style="left:600px;top:3157px"></div>

<!-- About -->
<svg class="abs" style="left:120px;top:3618px" width="420" height="380" role="img" aria-label="Portrait photo of the site author at the beach">
  <defs><linearGradient id="portraitBg" x1="0" y1="0" x2="0" y2="1"><stop offset="0" stop-color="#9aa8b2"/><stop offset="1" stop-color="#8a6a4c"/></linearGradient></defs>
  <path d="M30 150 C40 50 180 0 290 30 C400 70 420 220 360 300 C300 380 110 385 50 310 C15 265 25 200 30 150 Z" fill="var(--gold)"/>
  <path d="M36 150 C46 58 180 8 288 38 C392 76 410 220 352 296 C294 372 114 376 56 304 C22 262 31 200 36 150 Z" fill="url(#portraitBg)"/>
</svg>
<h2 class="abs script" style="left:596px;top:3615px;font-size:34px">I am Marla Quenby</h2>
<div class="rule" style="left:596px;top:3668px;width:80px"></div>
<p class="abs body-copy" style="left:596px;top:3698px;width:480px">Hello nature lovers! I'm Marla Quenby, a wildlife educator, busy Florida Master Naturalist, nature writer and photographer, busy mama of three kiddos, a playful Havanese puppy, two very chubby guinea pigs, and a giant tree frog. I have a passion for all things nature and I adore living in Southwest Florida. I will always be a California girl, but from the moment.</p>
<div class="abs script" style="left:596px;top:3864px;font-size:22px;color:#8a5a3a">Marla Quenby</div>
<div class="btn" style="left:596px;top:3916px;width:137px;height:46px">Read More</div>

<!-- Gallery -->
<h2 class="script section-title" style="top:4173px">Our Photo Gallery</h2>
<div class="rule" style="left:542px;top:4230px;width:116px"></div>
<svg class="abs" style="left:1040px;top:4196px" width="50" height="20" viewBox="0 0 50 20"><path d="M8 3 L2 10 L8 17 M42 3 L48 10 L42 17" fill="none" stroke="var(--ink)" stroke-width="2.2"/></svg>
<div class="gallery-thumb" role="img" aria-label="Photo of a small dark beetle held between fingers" style="left:104px;width:252px;top:4255px;height:189px;border:6px solid var(--parchment-light);background:linear-gradient(135deg,#5a8a44,#c9977e)"></div>
<div class="gallery-thumb" role="img" aria-label="Photo of a black vulture on fallen branches" style="left:362px;width:234px;background:linear-gradient(160deg,#8a9aa0,#4a443a)"></div>
<div class="gallery-thumb" role="img" aria-label="Photo of a marsh with trees under a cloudy blue sky" style="left:611px;width:235px;background:linear-gradient(180deg,#7a9cc8,#4e7a34)"></div>
<div class="gallery-thumb" role="img" aria-label="Photo of palmetto fronds and purple wildflowers" style="left:861px;width:234px;background:linear-gradient(135deg,#6a7a4a,#5a6a40)"></div>

<!-- Footer -->
<div class="abs" style="left:0;top:4660px;width:1200px;height:6px;background:var(--brown)"></div>
<svg class="nav-ribbon" style="top:4566px" viewBox="0 0 1200 200" width="1200" height="200">
  <path d="M72 22 H1140 L1120 62 L1140 110 H72 L92 62 Z" fill="#c9b57a"/>
  <path d="M100 14 H1100 V116 H100 Z" fill="var(--ribbon)"/>
  <path d="M112 22 H1088 M112 108 H1088" stroke="#b9a46a" stroke-width="1.5" stroke-dasharray="3 4"/>
</svg>
<div class="nav-link" style="left:229px;top:4626px">Home</div>
<div class="nav-link" style="left:328px;top:4626px">About Us</div>
<div class="nav-link" style="left:421px;top:4626px">Blog</div>
<div class="nav-link" style="left:793px;top:4626px">Gallery</div>
<div class="nav-link" style="left:890px;top:4626px">Reviews</div>
<div class="nav-link" style="left:989px;top:4626px">Contact</div>
<svg class="abs" style="left:1058px;top:4633px" width="18" height="18" viewBox="0 0 18 18"><circle cx="7.5" cy="7.5" r="5.5" fill="none" stroke="var(--brown)" stroke-width="2.4"/><path d="M11.5 11.5 L16 16" stroke="var(--brown)" stroke-width="2.8"/></svg>
<div class="logo-circle" style="left:518px;top:4566px">Hop Bright<br>Meadow</div>

<div class="subscribe-input">Enter The Email</div>
<div class="btn" style="left:533px;top:4758px;width:145px;height:48px;font-weight:500">Subscribe</div>
<div class="social" aria-label="Social link" style="left:793px"></div>
<div class="social" aria-label="Social link" style="left:848px"></div>
<div class="social" aria-label="Social link" style="left:901px"></div>
<div class="social" aria-label="Social link" style="left:955px"></div>
<div class="social" aria-label="Social link" style="left:1010px"></div>

<div class="copyright">&copy; Copyrights 2020 Hop Bright Meadow &nbsp;&nbsp; | &nbsp;&nbsp; All Rights Reserved</div>

</body>
</html>
```